Postcard Design January 2015

I need a postcard designed to introduce my company to potential new customers in the UK. My company is TW Page Works based in Chester and we represent one of Poland's leading and long established book printers. We offer competitive pricing, consistently high levels of print and binding quality and industry leading levels of customer service. We have been meeting the print requirements of UK publishers for more than 10 years.
Updates

```html
<!DOCTYPE html>
<html lang="en">
<head>
<meta charset="utf-8">
<title>TW Page Works – Postcard</title>
<link href="https://fonts.googleapis.com/css2?family=Alfa+Slab+One&family=Lato:wght@400;700;900&display=swap" rel="stylesheet">
<style>
  :root {
    --page-bg: #e9e9e9;
    --charcoal: #3a3a3a;
    --charcoal-dark: #262626;
    --orange: #f08a1c;
    --orange-light: #fbc531;
    --yellow: #f7cf1d;
    --red: #e3262c;
    --ink: #1e1e1e;
    --white: #ffffff;
    --photo-tone: #9aa6b6;
  }
  * { box-sizing: border-box; margin: 0; padding: 0; }
  html, body { width: 900px; height: 1200px; overflow: hidden; }
  body {
    position: relative;
    background: var(--page-bg);
    font-family: "Lato", Arial, sans-serif;
    color: var(--ink);
  }

  /* ---------- Front of card ---------- */
  .card-front {
    position: absolute; left: 100px; top: 45px;
    width: 695px; height: 515px;
    box-shadow: 0 6px 18px rgba(0,0,0,.25);
  }
  .card-front > svg { position: absolute; inset: 0; }
  .brand-photo {
    position: absolute; left: 552px; top: 45px; width: 88px; height: 67px;
    background: var(--photo-tone); border: 2px solid var(--white);
  }
  .brand-name {
    position: absolute; left: 500px; top: 122px; width: 195px;
    text-align: center; font-family: "Lato", Arial, sans-serif;
    font-weight: 900; font-size: 30px; line-height: 29px; color: var(--red);
    text-transform: uppercase;
  }
  .headline {
    position: absolute; right: 28px; top: 412px; text-align: right;
    font-family: "Alfa Slab One", Georgia, serif; font-weight: 400; text-transform: uppercase;
    text-shadow: 2px 2px 0 rgba(0,0,0,.45);
  }
  .headline-top { display: block; font-size: 32px; line-height: 38px; color: var(--yellow); letter-spacing: .5px; }
  .headline-bottom { display: block; font-size: 43px; line-height: 46px; color: var(--red); letter-spacing: 1px; }

  /* ---------- Back of card ---------- */
  .card-back {
    position: absolute; left: 100px; top: 622px;
    width: 690px; height: 535px;
    box-shadow: 0 6px 18px rgba(0,0,0,.25);
  }
  .card-back > svg { position: absolute; inset: 0; }
  .info-panel { position: absolute; left: 0; top: 0; width: 370px; height: 535px; }
  .section-pill {
    position: absolute; left: 100px; top: 25px; width: 158px; height: 38px;
    border-radius: 19px; background: var(--charcoal);
    box-shadow: 0 6px 8px rgba(0,0,0,.25);
    font-family: "Alfa Slab One", Georgia, serif; font-weight: 400; font-size: 22px;
    color: var(--yellow); text-align: center; line-height: 38px;
  }
  .service-list { position: absolute; left: 18px; top: 87px; width: 345px; list-style: none; }
  .service-list li {
    position: relative; padding-left: 23px; margin-bottom: 4px;
    font-size: 15px; line-height: 19px;
  }
  .tick { position: absolute; left: 0; top: 4px; width: 13px; height: 12px; }
  .highlights {
    position: absolute; left: 0; top: 288px; width: 353px; height: 95px;
    background: #0d0d0d; border-radius: 0 28px 28px 0;
    list-style: none; padding: 4px 0 0 16px;
  }
  .highlights li {
    position: relative; padding-left: 19px; color: var(--white);
    font-size: 15px; line-height: 28.5px;
  }
  .highlights li::before {
    content: ""; position: absolute; left: 0; top: 10px;
    width: 8px; height: 8px; border-radius: 50%; background: var(--yellow);
  }
  .contact { position: absolute; width: 370px; font-weight: 700; font-size: 15px; line-height: 20px; white-space: nowrap; }
  .contact-icon { display: inline-block; width: 14px; height: 14px; vertical-align: -2px; margin-right: 6px; }
  .contact-line-1 { top: 401px; left: 17px; }
  .contact-line-1 .phone { margin-left: 12px; }
  .contact-line-2 { top: 428px; left: 51px; }
  .contact-line-3 { top: 456px; left: 0; text-align: center; }
  .call-to-action {
    position: absolute; left: 18px; top: 486px; width: 345px; height: 25px;
    background: var(--charcoal); color: var(--yellow);
    font-weight: 700; font-size: 15px; line-height: 25px; text-align: center;
  }
  .stamp-box {
    position: absolute; left: 585px; top: 85px; width: 64px; height: 70px;
    border: 1px solid #8a8a8a;
  }
  .address-line { position: absolute; left: 478px; width: 171px; height: 1px; background: #555; }
</style>
</head>
<body>

<section class="card-front">
  <svg width="695" height="515" viewBox="0 0 695 515">
    <defs>
      <linearGradient id="frameGrey" x1="0" y1="0" x2="0" y2="1">
        <stop offset="0" stop-color="#5a5a5a"/><stop offset="1" stop-color="#2c2c2c"/>
      </linearGradient>
      <radialGradient id="sunburst" cx="0.55" cy="0.55" r="0.7">
        <stop offset="0" stop-color="#fde46a"/><stop offset="0.5" stop-color="#f9b52c"/><stop offset="1" stop-color="#ef8a1e"/>
      </radialGradient>
      <linearGradient id="booksTone" x1="0" y1="0" x2="1" y2="0">
        <stop offset="0" stop-color="#d6c84a" stop-opacity="0.55"/>
        <stop offset="0.5" stop-color="#e0663a" stop-opacity="0.45"/>
        <stop offset="1" stop-color="#f9b52c" stop-opacity="0"/>
      </linearGradient>
    </defs>
    <rect width="695" height="515" fill="url(#frameGrey)"/>
    <rect x="0" y="22" width="695" height="3" fill="var(--white)"/>
    <rect x="0" y="25" width="695" height="470" fill="url(#sunburst)"/>
    <rect x="0" y="110" width="590" height="380" fill="url(#booksTone)" role="img" aria-label="Illustration of a fan of colourful open books"/>
    <path d="M695,395 L410,398 C370,400 350,420 330,445 C310,470 300,487 270,487 L0,487 L0,515 L695,515 Z" fill="url(#frameGrey)" stroke="var(--white)" stroke-width="3"/>
  </svg>
  <div class="brand-photo" role="img" aria-label="Photo of the company's office building"></div>
  <div class="brand-name">TW Page<br>Works</div>
  <h1 class="headline">
    <span class="headline-top">Book Printing</span>
    <span class="headline-bottom">Made Easy</span>
  </h1>
</section>

<section class="card-back">
  <svg width="690" height="535" viewBox="0 0 690 535">
    <defs>
      <linearGradient id="panelOrange" x1="0" y1="0" x2="0.4" y2="1">
        <stop offset="0" stop-color="#f08a1c"/><stop offset="0.45" stop-color="#fbc531"/><stop offset="1" stop-color="#f08a1c"/>
      </linearGradient>
      <linearGradient id="stripGrey" x1="0" y1="0" x2="1" y2="0">
        <stop offset="0" stop-color="#2a2a2a"/><stop offset="1" stop-color="#6b6b6b"/>
      </linearGradient>
    </defs>
    <rect x="0" y="0" width="372" height="535" fill="url(#panelOrange)"/>
    <rect x="370" y="0" width="100" height="535" fill="url(#stripGrey)"/>
    <path d="M387,0 L690,0 L690,535 L455,535 L455,292 C455,262 388,262 387,232 Z" fill="var(--white)"/>
  </svg>

  <div class="info-panel">
    <h2 class="section-pill">SERVICES</h2>
    <ul class="service-list">
      <li><svg class="tick" viewBox="0 0 13 12"><path d="M1,6 L5,10 L12,1" fill="none" stroke="#fff" stroke-width="2"/></svg>We produce paperback and hardback books in mono or full colour. Binding options include sewn, perfect, Wiro-o and saddle stitched</li>
      <li><svg class="tick" viewBox="0 0 13 12"><path d="M1,6 L5,10 L12,1" fill="none" stroke="#fff" stroke-width="2"/></svg>Print finishing includes lamination, spot UV and foil stamping</li>
      <li><svg class="tick" viewBox="0 0 13 12"><path d="M1,6 L5,10 L12,1" fill="none" stroke="#fff" stroke-width="2"/></svg>We have state of the art production equipment, use top quality materials and follow strict quality control procedures</li>
      <li><svg class="tick" viewBox="0 0 13 12"><path d="M1,6 L5,10 L12,1" fill="none" stroke="#fff" stroke-width="2"/></svg>We have weekly shipments in to the UK</li>
    </ul>
    <ul class="highlights">
      <li>High quality book printing and binding</li>
      <li>Competitive pricing</li>
      <li>Excellent customer service</li>
    </ul>
    <p class="contact contact-line-1">
      <svg class="contact-icon" viewBox="0 0 14 14"><path d="M7,1 L1,7 H3 V13 H6 V9 H8 V13 H11 V7 H13 Z" fill="#fff"/></svg>Rowan Lodge
      <span class="phone"><svg class="contact-icon" viewBox="0 0 14 14"><path d="M3,1 L5.5,1 L6.5,4.5 L5,6 C6,8 7,9 9,10 L10.5,8.5 L13,9.5 L13,12 C13,12.8 12.4,13 11.5,13 C6,12.5 1.5,8 1,3 C1,2 1.6,1 3,1 Z" fill="#fff"/></svg>01632 960418</span>
    </p>
    <p class="contact contact-line-2">
      <svg class="contact-icon" viewBox="0 0 14 14"><rect x="1" y="3" width="12" height="8.5" fill="#fff"/><path d="M1,3 L7,8 L13,3" fill="none" stroke="#f3a324" stroke-width="1.2"/></svg>hello@twpageworks.co.uk
    </p>
    <p class="contact contact-line-3">Field Lane, Westbrook, Chester, CH3 0ZZ</p>
    <p class="call-to-action">Please contact us for a quotation or a meeting</p>
  </div>

  <div class="stamp-box"></div>
  <div class="address-line" style="top:256px"></div>
  <div class="address-line" style="top:288px"></div>
  <div class="address-line" style="top:320px"></div>
</section>

</body>
</html>
```